Marwick Family Chiropractic Stationary

The letterhead and business card must have our logo.
We would like to see the logo used in different ways ( It can be expanded upon in the stationary.)
Please use the the same or similar colors.
Must be eye catching and memorable.
Must be easy to read

Reason: The doctor has been too busy to make any final decisions. He would like to give himself a little more time.

Target Market(s)

Chiropractic Healthcare

Industry/Entity Type

Business

Requirements
Must have
• Dr. Leonard Marwick D.C.
Chiropractor

860-555-0183

417 Birchfield Road, 2nd Floor
Alderbrook, CT 06091

drmarwick@marwickspine.example
www.marwickspine.example
www.facebook.com/MarwickFamilySpine
Should not have
• should not be difficult to read

```html
<!DOCTYPE html>
<html lang="en">
<head>
<meta charset="utf-8">
<title>Marwick Family Chiropractic – Business Cards</title>
<link href="https://fonts.googleapis.com/css2?family=Montserrat:wght@600;700&family=Open+Sans:wght@400;600&display=swap" rel="stylesheet">
<style>
  :root {
    --stage: #ece6dc;
    --label: #2b2420;
    --green: #2e9a48;
    --leaf-light: #a9cf5a;
    --taupe: #9c9184;
    --dark-brown: #2a221c;
    --swoosh-dark: #3a2e26;
    --ink: #444444;
    --white: #ffffff;
    --black: #0a0a0a;
  }
  * { box-sizing: border-box; margin: 0; padding: 0; }
  html, body { width: 1200px; height: 788px; overflow: hidden; }
  body {
    position: relative;
    background: var(--stage);
    font-family: "Open Sans", sans-serif;
  }
  .side-label {
    position: absolute;
    width: 525px;
    text-align: center;
    font-size: 21px;
    color: var(--label);
  }
  .card {
    position: absolute;
    width: 525px;
    height: 300px;
    border-radius: 22px;
    overflow: hidden;
    box-shadow: 0 6px 14px rgba(0,0,0,0.25);
  }
  .card--white { background: var(--white); }
  .card--brown { background: var(--dark-brown); }
  .card--black { background: var(--black); }

  .swoosh { position: absolute; }
  .swoosh--top { right: 0; top: 0; }
  .swoosh--bottom { left: 0; bottom: 0; }

  .brand {
    position: absolute;
    display: flex;
    flex-direction: column;
    align-items: center;
    font-family: "Montserrat", sans-serif;
    font-weight: 700;
    line-height: 1;
    text-align: center;
  }
  .brand__dot { border-radius: 50%; margin-bottom: 16px; }
  .brand__name { letter-spacing: 0.5px; }
  .brand__line { margin-top: 6px; letter-spacing: 0.4px; }

  .brand--front { left: 15px; top: 100px; width: 200px; color: var(--green); }
  .brand--front .brand__dot { width: 72px; height: 72px; background: var(--green); }
  .brand--front .brand__name { font-size: 28px; }
  .brand--front .brand__line { font-size: 11px; color: var(--swoosh-dark); }

  .divider {
    position: absolute;
    left: 225px; top: 70px;
    width: 1px; height: 158px;
    background: #9a9a9a;
  }
  .contact {
    position: absolute;
    left: 284px; top: 68px;
    color: var(--ink);
    font-size: 12px;
  }
  .contact__name {
    font-family: "Montserrat", sans-serif;
    font-weight: 700;
    font-size: 15px;
    color: var(--green);
  }
  .contact__title { font-weight: 600; font-size: 11.5px; margin-bottom: 8px; }
  .contact__row { display: flex; margin-top: 7px; line-height: 15px; }
  .contact__key { font-weight: 600; font-style: italic; margin-right: 5px; flex: none; }

  .brand--back1 { left: 0; width: 525px; top: 36px; color: var(--green); }
  .brand--back1 .brand__dot { width: 118px; height: 118px; background: var(--green); }
  .brand--back1 .brand__name { font-size: 33px; }
  .brand--back1 .brand__line { font-size: 13px; color: var(--swoosh-dark); }

  .brand--back2 { left: 0; width: 525px; top: 100px; color: var(--green); }
  .brand--back2 .brand__name { font-size: 58px; letter-spacing: 1px; }
  .brand--back2 .brand__line { font-size: 24px; margin-top: 12px; color: var(--white); }

  .brand--back3 { left: 0; width: 525px; top: 36px; color: var(--leaf-light); }
  .brand--back3 .brand__dot { width: 118px; height: 118px; background: var(--leaf-light); }
  .brand--back3 .brand__name { font-size: 32px; }
  .brand--back3 .brand__line { font-size: 13px; color: var(--taupe); }

  .web {
    position: absolute;
    left: 0; width: 525px;
    bottom: 20px;
    text-align: center;
    font-size: 15px;
  }
  .card--white .web { color: var(--ink); }
  .card--brown .web, .card--black .web { color: var(--white); }
</style>
</head>
<body>

  <div class="side-label" style="left:59px; top:33px;">Front</div>
  <div class="side-label" style="left:622px; top:33px;">Back - 1</div>
  <div class="side-label" style="left:54px; top:404px;">Back - 2</div>
  <div class="side-label" style="left:622px; top:404px;">Back - 3</div>

  <section class="card card--white" style="left:59px; top:79px;">
    <svg class="swoosh swoosh--top" width="110" height="40" viewBox="0 0 110 40" aria-hidden="true">
      <path d="M0 0 H110 V32 C90 14 50 3 0 0 Z" fill="var(--green)"/>
      <path d="M10 2 C60 5 95 18 110 38 V30 C92 14 55 4 10 2 Z" fill="var(--swoosh-dark)"/>
    </svg>
    <svg class="swoosh swoosh--bottom" width="110" height="42" viewBox="0 0 110 42" aria-hidden="true">
      <path d="M0 14 C20 30 55 40 110 42 H0 Z" fill="var(--green)"/>
      <path d="M0 0 C22 18 55 30 100 36 C55 34 22 24 0 10 Z" fill="var(--swoosh-dark)"/>
    </svg>

    <div class="brand brand--front">
      <span class="brand__dot"></span>
      <span class="brand__name">MARWICK</span>
      <span class="brand__line">FAMILY CHIROPRACTIC</span>
    </div>

    <div class="divider"></div>

    <div class="contact">
      <div class="contact__name">Dr. Leonard Marwick D.C.</div>
      <div class="contact__title">Chiropractor</div>
      <div class="contact__row"><span class="contact__key">ph :</span><span>860-555-0183</span></div>
      <div class="contact__row"><span class="contact__key">e :</span><span>drmarwick@marwickspine.example</span></div>
      <div class="contact__row"><span class="contact__key">w :</span><span>www.marwickspine.example</span></div>
      <div class="contact__row"><span class="contact__key">fb :</span><span>MarwickFamilySpine</span></div>
      <div class="contact__row"><span class="contact__key">a :</span><span>417 Birchfield Road<br>2nd Floor, Alderbrook, CT 06091</span></div>
    </div>
  </section>

  <section class="card card--white" style="left:622px; top:75px;">
    <div class="brand brand--back1">
      <span class="brand__dot"></span>
      <span class="brand__name">MARWICK</span>
      <span class="brand__line">FAMILY CHIROPRACTIC</span>
    </div>
    <div class="web">www.marwickspine.example</div>
  </section>

  <section class="card card--brown" style="left:54px; top:445px;">
    <div class="brand brand--back2">
      <span class="brand__name">MARWICK</span>
      <span class="brand__line">FAMILY CHIROPRACTIC</span>
    </div>
    <div class="web">www.marwickspine.example</div>
  </section>

  <section class="card card--black" style="left:622px; top:445px;">
    <div class="brand brand--back3">
      <span class="brand__dot"></span>
      <span class="brand__name">MARWICK</span>
      <span class="brand__line">FAMILY CHIROPRACTIC</span>
    </div>
    <div class="web">www.marwickspine.example</div>
  </section>

</body>
</html>
```